New, modern business card for growing audiology practice

We need a new business card for our audiology practice. Our logo and website have recently changed (more modern) and we want our business cards to reflect this change.
We conduct hearing tests, perform earwax removals, and fit & dispense hearing aids to our patients. We are a family owned practice in which the owner is the one who works directly with the patient. I have attached logos in various formats to use, as well as two ideas I found on this website; as well as a scanned copy of our current logo. Good luck!

Industry/Entity Type

Business

Contact Information for Business Card

Company name: Tolvera Hearing Center
Provider name: Peter Wolstenby, Au.D. F/NSB
Phone number: (440) 683-5127
Address: 837 W. Lindell Ave. Ashcombe Falls, TN 38142
email: tolverahearing@postvane.com
website: tolverahearing.com

Colors
000000
aaaaaa
dbdbdb
cacaca
9bcb3c
afd23c
cadf82
b1b1b1

Requirements
Must have
• My card must include information in the "details" section. In the attached images, I found a few that I liked and I would like to model after - "brisky bouncin'" and "Sound Method Center".
• Must be horizontal.
• Must include logos provided. I uploaded them in various file formats and various ways.
• Must match logo font, if possible, if not, please get as close as you can.
Nice to have
• I really like the idea of having a color on one side with just the logo and company name and the contact information and provider name on the other side. I also really like the idea of having the main color dominating on the logo/company side with accent of that same color on the contact side of the card.
Should not have
• Must not be vertical.

```html
<!DOCTYPE html>
<html lang="en">
<head>
<meta charset="utf-8">
<title>Tolvera Hearing Center — Business Card</title>
<link rel="stylesheet" href="https://fonts.googleapis.com/css2?family=Lato:wght@400;700&family=Source+Sans+3:wght@400;600;700&display=swap">
<style>
  :root {
    --ink: #000000;
    --lime: #afd23c;
    --lime-deep: #9bcb3c;
    --stone: #dbdbdb;
    --mist: #cacaca;
    --paper: #ffffff;
    --backdrop: #e9e9e9;
    --charcoal: #222222;
    --muted: #b1b1b1;
  }
  * { box-sizing: border-box; margin: 0; padding: 0; }
  html, body {
    width: 1200px;
    height: 900px;
    overflow: hidden;
    background: var(--backdrop);
  }
  .canvas {
    position: relative;
    width: 1200px;
    height: 900px;
  }

  /* Front: contact side */
  .card-front {
    position: absolute;
    left: 178px;
    top: 74px;
    width: 588px;
    height: 364px;
    background: var(--ink);
    overflow: hidden;
    font-family: "Source Sans 3", sans-serif;
    color: var(--paper);
    box-shadow: 0 10px 28px rgba(0,0,0,0.18);
  }
  .accent-panel {
    position: absolute;
    right: 0;
    top: 0;
    width: 176px;
    height: 100%;
    background: var(--lime);
  }
  .provider {
    position: absolute;
    left: 31px;
    top: 46px;
  }
  .provider-name {
    font-weight: 700;
    font-size: 19px;
    letter-spacing: 0.2px;
    color: var(--lime);
    text-transform: uppercase;
    line-height: 1.1;
  }
  .provider-name .comma { color: var(--paper); }
  .provider-title {
    font-size: 15px;
    color: var(--stone);
    text-transform: uppercase;
    margin-top: 3px;
  }
  .contact {
    position: absolute;
    left: 30px;
    list-style: none;
    font-size: 16px;
    line-height: 22px;
  }
  .contact-address { top: 193px; }
  .contact-reach { top: 253px; }
  .contact li {
    display: flex;
    align-items: flex-start;
  }
  .contact .icon {
    width: 12px;
    height: 12px;
    margin-top: 5px;
    margin-right: 8px;
    flex: none;
    fill: var(--lime);
  }
  .contact .indent { padding-left: 20px; }

  /* Back: brand side */
  .card-back {
    position: absolute;
    left: 388px;
    top: 505px;
    width: 567px;
    height: 352px;
    background: var(--paper);
    font-family: "Lato", sans-serif;
    box-shadow: 0 10px 28px rgba(0,0,0,0.16);
  }
  .brand {
    position: absolute;
    left: 0;
    right: 0;
    top: 154px;
    display: flex;
    justify-content: center;
    align-items: center;
    gap: 12px;
  }
  .brand-dot {
    width: 16px;
    height: 16px;
    border-radius: 50%;
    background: var(--lime);
  }
  .brand-name {
    font-size: 30px;
    font-weight: 400;
    color: var(--charcoal);
    text-transform: uppercase;
    letter-spacing: 0.4px;
  }
  .web {
    position: absolute;
    left: 0;
    right: 0;
    top: 284px;
    text-align: center;
    font-family: "Source Sans 3", sans-serif;
    font-weight: 700;
    font-size: 16px;
    color: var(--charcoal);
  }
  .web .domain { color: var(--lime-deep); }
</style>
</head>
<body>
<main class="canvas">

  <section class="card-front" aria-label="Business card, contact side">
    <div class="accent-panel"></div>

    <header class="provider">
      <h1 class="provider-name">Peter Wolstenby<span class="comma">,</span></h1>
      <p class="provider-title">Au.D. F/NSB</p>
    </header>

    <ul class="contact contact-address">
      <li>
        <svg class="icon" viewBox="0 0 12 12" aria-hidden="true"><path d="M6 0a4 4 0 0 0-4 4c0 3 4 8 4 8s4-5 4-8a4 4 0 0 0-4-4zm0 5.6A1.6 1.6 0 1 1 6 2.4a1.6 1.6 0 0 1 0 3.2z"/></svg>
        <span>837 W. Lindell</span>
      </li>
      <li class="indent">Ave. Ashcombe Falls, TN 38142</li>
    </ul>

    <ul class="contact contact-reach">
      <li>
        <svg class="icon" viewBox="0 0 12 12" aria-hidden="true"><path d="M2.4 0.5l2 2.2-1 1.3c.7 1.6 2 2.9 3.6 3.6l1.3-1 2.2 2-1.2 2.2C4.6 10.6 1.4 7.4.2 1.7z"/></svg>
        <span>(440) 683-5127</span>
      </li>
      <li>
        <svg class="icon" viewBox="0 0 12 12" aria-hidden="true"><path d="M0 2.5h12v7H0z"/><path d="M0.6 3.2L6 6.8l5.4-3.6" fill="none" stroke="#000" stroke-width="1"/></svg>
        <span>tolverahearing@postvane.com</span>
      </li>
      <li>
        <svg class="icon" viewBox="0 0 12 12" aria-hidden="true"><circle cx="6" cy="6" r="5.5"/><path d="M0.8 6h10.4M6 0.6c-2.6 3-2.6 7.8 0 10.8M6 0.6c2.6 3 2.6 7.8 0 10.8" fill="none" stroke="#000" stroke-width="0.9"/></svg>
        <span>www.tolverahearing.com</span>
      </li>
    </ul>
  </section>

  <section class="card-back" aria-label="Business card, brand side">
    <div class="brand">
      <span class="brand-dot"></span>
      <span class="brand-name">Tolvera Hearing Center</span>
    </div>
    <p class="web">www.<span class="domain">tolverahearing</span>.com</p>
  </section>

</main>
</body>
</html>
```